Website for software company "velora"

We need a website for our software company/startup named "velora". We are developing several products (currently 3 standard-software products) which are all in different sectors, but all our products are available for Laptops/PC/Mobile Phones/Tablets, ... We do also create custom software and support our customers with consulting to optimize their processes.
We already have a Logo which you can find in the attached files.
We are a young team of 4 members (two founders and 2 employees).

To get an idea of our products -> the first one is a planning software for healthcare organizations (eg. BlueHaven, firebrigade, pharmacy), the second one is a booking software for sport clubs and the third one is a competition software for sports hunting. You see very diverse. Include or ignore this info of our products as you like.

The design has to be a bootstrap 4 (or higher) design. We have licenced FontAwesome as iconset. Responsive design should come without saying.

• Starting page, product pages, news section, contact, team, services

```html
<!DOCTYPE html>
<html lang="en">
<head>
<meta charset="utf-8">
<title>velora – Custom Software and Support</title>
<link rel="stylesheet" href="https://fonts.googleapis.com/css2?family=Oswald:wght@500;600;700&family=Mulish:wght@400;600;700&family=Montserrat:wght@600;700;800&display=swap">
<style>
:root{
  --orange:#f47b2a;
  --orange-deep:#ee6a1c;
  --ink:#2a2d36;
  --text:#555a62;
  --muted:#777c84;
  --line:#e2e4e8;
  --peach:#fbefe9;
  --footer:#2b2f3a;
  --grey-bg:#f1f2f4;
  --white:#fff;
}
*{box-sizing:border-box;margin:0;padding:0}
html,body{width:1200px;height:3156px;overflow:hidden}
body{position:relative;background:var(--white);font-family:'Mulish',sans-serif;color:var(--text)}
.abs{position:absolute}

/* header */
.site-header{position:absolute;left:0;top:0;width:1200px;height:69px;background:var(--white)}
.brand{position:absolute;display:flex;align-items:center;gap:10px;font-family:'Montserrat',sans-serif;font-weight:800;letter-spacing:1px}
.brand-mark{width:22px;height:22px;background:var(--orange)}
.site-header .brand{left:129px;top:14px;font-size:38px;line-height:40px;color:var(--ink)}
.nav{position:absolute;top:21px;left:429px;display:flex;gap:0;font-size:16px;color:var(--ink)}
.nav a{color:inherit;text-decoration:none;padding:3px 8px;margin-right:18px;line-height:20px}
.nav a.active{color:var(--orange);border:1px solid var(--orange)}
.cta{position:absolute;left:933px;top:16px;width:135px;height:36px;background:var(--orange);color:var(--white);font-size:16px;line-height:36px;text-align:center;padding-left:12px}
.cta::before{content:"";position:absolute;left:0;top:0;border-style:solid;border-width:18px 0 18px 20px;border-color:transparent transparent transparent var(--ink)}

/* hero */
.hero{position:absolute;left:0;top:69px;width:1200px;height:579px;background:linear-gradient(100deg,#b9bcc3 0%,#7b7f89 30%,#3e4656 55%,#31405e 75%,#5a6a8a 100%)}
.hero h1{position:absolute;left:793px;top:214px;font-family:'Oswald',sans-serif;font-weight:700;font-size:52px;line-height:58px;color:var(--white);text-transform:uppercase;letter-spacing:.5px}
.btn{display:inline-flex;align-items:center;gap:6px;background:var(--orange);color:var(--white);font-family:'Montserrat',sans-serif;font-weight:700;text-decoration:none}
.btn::after{content:"";border-style:solid;border-color:transparent transparent transparent currentColor}
.btn-lg{position:absolute;left:800px;top:409px;height:47px;padding:0 18px;font-family:'Mulish',sans-serif;font-size:19px}
.btn-lg::after{border-width:7px 0 7px 8px}
.btn-sm{height:24px;padding:0 9px;font-size:10px}
.btn-sm::after{border-width:4px 0 4px 5px}
.btn-md{height:34px;padding:0 13px;font-family:'Mulish',sans-serif;font-size:14px}
.btn-md::after{border-width:5px 0 5px 6px}
.dots{position:absolute;left:567px;top:544px;display:flex;gap:6px}
.dots span{width:8px;height:6px;background:var(--white)}
.dots span.on{background:var(--orange)}

/* section titles */
.section-title{position:absolute;left:0;width:1200px;text-align:center;font-family:'Oswald',sans-serif;font-weight:600;font-size:29px;color:var(--ink);text-transform:uppercase}
.section-title::after{content:"";display:block;width:44px;height:2px;background:var(--ink);margin:12px auto 0}

/* products */
.product-card{position:absolute;top:768px;width:302px;height:394px;background:var(--peach);padding:13px}
.product-card .inner{position:relative;width:100%;height:100%;background:var(--white);text-align:center}
.product-photo{height:121px}
.product-icon{position:absolute;left:50%;top:88px;width:64px;height:64px;margin-left:-32px;border-radius:50%;background:var(--orange);border:4px solid var(--white);display:flex;align-items:center;justify-content:center}
.product-card h3{margin-top:42px;font-family:'Montserrat',sans-serif;font-weight:700;font-size:14px;line-height:19px;color:var(--ink);text-transform:uppercase;padding:0 30px}
.product-card p{font-size:12.5px;line-height:18px;color:var(--text);padding:0 18px;margin-top:14px;height:96px}
.product-card .btn{margin-top:12px}

/* welcome */
.welcome-band{position:absolute;left:0;top:1217px;width:621px;height:488px;background:linear-gradient(120deg,#f58a3c,#f26f1f 60%,#f79a55)}
.welcome-photo{position:absolute;left:136px;top:1250px;width:634px;height:422px;background:linear-gradient(135deg,#d9dbde 0%,#9aa2ac 40%,#2d5a92 60%,#bfc3c8 100%)}
.welcome-box{position:absolute;left:621px;top:1289px;width:460px;height:355px;background:var(--white);box-shadow:0 8px 30px rgba(0,0,0,.08);padding:32px 51px 0 40px}
.welcome-box h2{font-family:'Oswald',sans-serif;font-weight:600;font-size:28px;color:var(--ink);text-transform:uppercase}
.welcome-box h2::after{content:"";display:block;width:100px;height:2px;background:var(--ink);margin-top:8px}
.welcome-box p{margin-top:22px;font-size:13.6px;line-height:19.3px;text-align:justify;color:var(--text)}
.welcome-box .btn{margin-top:26px;height:34px}

/* services */
.services{position:absolute;left:0;top:1705px;width:1200px;height:587px;background:linear-gradient(90deg,#eceef1 0%,#fafafb 45%,#fff 100%)}
.service-photo{position:absolute;left:0;top:1840px;width:505px;height:452px;background:linear-gradient(90deg,#dfe2e6,#cfd3d8 50%,#eef0f2)}
.service{position:absolute;left:570px;width:498px}
.service-icon{position:absolute;left:1px;top:3px;width:88px;height:84px;background:var(--orange);display:flex;align-items:center;justify-content:center}
.service h3{position:absolute;left:112px;top:0;font-family:'Montserrat',sans-serif;font-weight:700;font-size:15px;color:var(--ink);text-transform:uppercase}
.service p{position:absolute;left:112px;top:26px;width:386px;font-size:13.4px;line-height:16.8px;color:var(--text);text-align:justify}
.divider{position:absolute;left:561px;width:507px;height:1px;background:var(--line)}

/* blog */
.blog{position:absolute;left:0;top:2292px;width:1200px;height:539px;background:var(--grey-bg)}
.blog-card{position:absolute;top:2415px;width:288px;height:373px;background:var(--white)}
.blog-photo{height:155px}
.blog-body{padding:21px 27px 0}
.blog-date{font-size:12px;color:var(--muted)}
.blog-card h3{margin-top:11px;font-family:'Mulish',sans-serif;font-weight:600;font-size:16px;line-height:21px;color:var(--ink)}
.blog-card p{margin-top:12px;font-size:13px;line-height:16.5px;color:var(--text)}
.blog-card .btn{margin-top:16px;height:26px}

/* footer */
.site-footer{position:absolute;left:0;top:2831px;width:1200px;height:325px;background:var(--footer);color:var(--white)}
.site-footer .brand{left:139px;top:106px;font-size:50px;line-height:52px;color:var(--white);font-weight:700}
.site-footer .brand-mark{background:var(--white);width:26px;height:26px}
.foot-col{position:absolute;top:43px}
.foot-col h4{font-family:'Montserrat',sans-serif;font-weight:700;font-size:12.5px;letter-spacing:.5px;text-transform:uppercase}
.foot-menu{list-style:none;margin-top:26px;font-size:11.5px;line-height:20px;text-transform:uppercase}
.foot-item{position:relative;padding-left:33px;font-size:11.8px;line-height:15.5px}
.foot-item .ico{position:absolute;left:0;top:3px;width:23px;height:23px;border-radius:50%;background:var(--white);display:flex;align-items:center;justify-content:center}
.foot-rule{position:absolute;left:134px;top:253px;width:933px;height:1px;background:rgba(255,255,255,.18)}
.copyright{position:absolute;left:0;top:284px;width:1200px;text-align:center;font-size:12.5px}
</style>
</head>
<body>

<header class="site-header">
  <div class="brand"><span class="brand-mark"></span>VELORA</div>
  <nav class="nav">
    <a class="active" href="#">Home</a>
    <a href="#">About Us</a>
    <a href="#">Our Products</a>
    <a href="#" style="margin-left:8px">Blog</a>
    <a href="#">Contact Us</a>
  </nav>
  <div class="cta">Get in Touch</div>
</header>

<section class="hero" role="img" aria-label="Hands typing on a laptop overlaid with glowing blue and red binary digits">
  <h1>Create custom<br>software and<br>support</h1>
  <a class="btn btn-lg" href="#">Read more</a>
  <div class="dots"><span></span><span></span><span class="on"></span><span></span><span></span></div>
</section>

<h2 class="section-title" style="top:683px">Our Products</h2>

<article class="product-card" style="left:129px">
  <div class="inner">
    <div class="product-photo" role="img" aria-label="Pharmacy shelves stocked with medicine boxes" style="background:linear-gradient(90deg,#dfe6ee,#c6d2de,#e8ecf1)"></div>
    <div class="product-icon"><svg width="34" height="30" viewBox="0 0 34 30" fill="none" stroke="#fff" stroke-width="2.4" stroke-linejoin="round"><path d="M17 28S3 19 3 10a7 7 0 0 1 14-2 7 7 0 0 1 14 2c0 9-14 18-14 18z"/><path d="M6 15h7l2-4 3 8 2-4h8"/></svg></div>
    <h3>Healthcare organizations</h3>
    <p>Lorem ipsum dolor sit amet, conse ctetur adipiscing elit, sed do eiusmod tempor incididunt ut labore et dolore magna aliqua. Ut enim.</p>
    <a class="btn btn-sm" href="#">Read more</a>
  </div>
</article>

<article class="product-card" style="left:449px">
  <div class="inner">
    <div class="product-photo" role="img" aria-label="Football players running across a green field" style="background:linear-gradient(180deg,#5b6b3a,#7f9a45 60%,#6a8a3a)"></div>
    <div class="product-icon"><svg width="32" height="32" viewBox="0 0 32 32" fill="none" stroke="#fff" stroke-width="2.4"><circle cx="16" cy="16" r="13"/><path d="M16 10l5 4-2 6h-6l-2-6z" fill="#fff"/></svg></div>
    <h3 style="margin-top:42px">Sport clubs</h3>
    <p style="margin-top:14px;height:115px">ed ut perspiciatis unde omnis iste natus error sit voluptatem accusa ntium doloremque laudantium, totam rem aperiam, eaque ipsa quae ab illo inventore veritatis et quasi.</p>
    <a class="btn btn-sm" href="#" style="margin-top:12px">Read more</a>
  </div>
</article>

<article class="product-card" style="left:767px">
  <div class="inner">
    <div class="product-photo" role="img" aria-label="Hunter silhouetted against a sunset sky" style="background:linear-gradient(180deg,#3f4650,#8a6a52 70%,#3a3028)"></div>
    <div class="product-icon"><svg width="32" height="32" viewBox="0 0 32 32" fill="none" stroke="#fff" stroke-width="2.4" stroke-linecap="round"><path d="M5 5l22 22M27 5L5 27"/><path d="M5 5h6M5 5v6M27 5h-6M27 5v6"/></svg></div>
    <h3 style="margin-top:42px">Sports hunting</h3>
    <p style="margin-top:14px;height:115px">At vero eos et accusamus et iusto odio dignissimos ducimus qui blanditiis praesentium voluptatum deleniti atque corrupti quos dolores et quas molestias excepturi sint.</p>
    <a class="btn btn-sm" href="#" style="margin-top:12px">Read more</a>
  </div>
</article>

<div class="welcome-band"></div>
<div class="welcome-photo" role="img" aria-label="Person working on a laptop with floating labels for SEO, web optimization, project development and website ranking"></div>
<section class="welcome-box">
  <h2>Welcome to velora</h2>
  <p>At vero eos et accusamus et iusto odio dignissimos ducimus qui blanditiis praesentium voluptatum deleniti atque corrupti quos dolores et quas molestias excepturi sint occaecati cupiditate non provident, similique sunt in culpa qui officia deserunt mollitia animi, id est laborum et dolorum fuga. Et harum quidem rerum facilis est et expedita distinctio. Nam libero tempore, cum soluta nobis est eligendi optio cumque nihil impedit quo minus id</p>
  <a class="btn btn-md" href="#">Read more</a>
</section>

<section class="services"></section>
<div class="service-photo" role="img" aria-label="Smiling man with glasses in a bright office"></div>
<h2 class="section-title" style="top:1755px">Our Service Offerings</h2>

<div class="service" style="top:1853px">
  <div class="service-icon"><svg width="56" height="46" viewBox="0 0 56 46" fill="none" stroke="#fff" stroke-width="2.2"><rect x="2" y="2" width="40" height="30"/><rect x="12" y="12" width="42" height="32" fill="#f47b2a"/><path d="M12 19h42"/><path d="M25 27l-4 4 4 4M39 27l4 4-4 4M30 36l4-10"/></svg></div>
  <h3>Custom software</h3>
  <p>At vero eos et accusamus et iusto odio dignissimos ducimus qui blanditiis praesentium voluptatum deleniti atque corrupti quos dolores et quas molestias excepturi sint occaecati cupiditate.</p>
</div>
<div class="divider" style="top:1972px"></div>

<div class="service" style="top:1994px">
  <div class="service-icon"><svg width="52" height="48" viewBox="0 0 52 48" fill="none" stroke="#fff" stroke-width="2.2"><rect x="3" y="3" width="46" height="32"/><path d="M3 10h46M20 35l-3 9h18l-3-9M13 44h26"/><path d="M20 18l-4 4 4 4M32 18l4 4-4 4M24 28l4-12"/></svg></div>
  <h3>Web development</h3>
  <p>At vero eos et accusamus et iusto odio dignissimos ducimus qui blanditiis praesentium voluptatum deleniti atque corrupti quos dolores et quas molestias excepturi sint occaecati cupiditate.</p>
</div>
<div class="divider" style="top:2117px"></div>

<div class="service" style="top:2138px">
  <div class="service-icon"><svg width="40" height="50" viewBox="0 0 40 50" fill="none" stroke="#fff" stroke-width="2.2"><path d="M3 3h24l10 10v34H3z"/><path d="M27 3v10h10"/><path d="M12 20a8 8 0 1 1 4 7"/><path d="M12 15v5h5"/><path d="M10 34h20M10 40h20"/></svg></div>
  <h3>Testing</h3>
  <p>At vero eos et accusamus et iusto odio dignissimos ducimus qui blanditiis praesentium voluptatum deleniti atque corrupti quos dolores et quas molestias excepturi sint occaecati cupiditate.</p>
</div>

<section class="blog"></section>
<h2 class="section-title" style="top:2326px">Latest Blog</h2>

<article class="blog-card" style="left:129px">
  <div class="blog-photo" role="img" aria-label="Team of colleagues gathered around a laptop" style="background:linear-gradient(135deg,#cfd5db,#8f99a5 50%,#e3e6ea)"></div>
  <div class="blog-body">
    <div class="blog-date">April 16, 2022</div>
    <h3>Lorem Ipsum is simply dumm text of the printing</h3>
    <p>Lorem Ipsum is simply dummy text of the printing and typesetting industry. Lorem Ipsum has.</p>
    <a class="btn btn-sm" href="#">Read more</a>
  </div>
</article>

<article class="blog-card" style="left:456px">
  <div class="blog-photo" role="img" aria-label="Developer pointing at code on a monitor" style="background:linear-gradient(135deg,#3a3f46,#1f252d 50%,#6a707a)"></div>
  <div class="blog-body">
    <div class="blog-date">April 16, 2022</div>
    <h3>There are many variations of passages of Lorem Ips</h3>
    <p>Lorem Ipsum is simply dummy text of the printing and typesetting industry. Lorem Ipsum has.</p>
    <a class="btn btn-sm" href="#">Read more</a>
  </div>
</article>

<article class="blog-card" style="left:781px">
  <div class="blog-photo" role="img" aria-label="Young team working together at a desk by tall windows" style="background:linear-gradient(135deg,#e6eaee,#b3bcc6 50%,#d7dce2)"></div>
  <div class="blog-body">
    <div class="blog-date">April 16, 2022</div>
    <h3>It is a long established fact that a reader will be</h3>
    <p>Lorem Ipsum is simply dummy text of the printing and typesetting industry. Lorem Ipsum has.</p>
    <a class="btn btn-sm" href="#">Read more</a>
  </div>
</article>

<footer class="site-footer">
  <div class="brand"><span class="brand-mark"></span>VELORA</div>

  <div class="foot-col" style="left:453px">
    <h4>Menu</h4>
    <ul class="foot-menu">
      <li>Home</li><li>About Us</li><li>Our Products</li><li>Blog</li><li>Contact Us</li>
    </ul>
  </div>

  <div class="foot-col" style="left:650px">
    <h4>Contact Us</h4>
    <div class="foot-item" style="margin-top:30px">
      <span class="ico"><svg width="10" height="13" viewBox="0 0 10 13"><path d="M5 0a5 5 0 0 1 5 5c0 3-5 8-5 8S0 8 0 5a5 5 0 0 1 5-5z" fill="#2b2f3a"/><circle cx="5" cy="5" r="1.8" fill="#fff"/></svg></span>
      4150 Larkspur Ave Suite 12<br>Denver, CO 80211
    </div>
    <div class="foot-item" style="margin-top:19px">
      <span class="ico"><svg width="11" height="11" viewBox="0 0 11 11"><path d="M2 0l2 2.5-1.2 1.5a7 7 0 0 0 4.2 4.2L8.5 7 11 9l-1.5 2C4 11 0 7 0 1.5z" fill="#2b2f3a"/></svg></span>
      Call Us<br>+1 555 010 2040
    </div>
    <div class="foot-item" style="margin-top:21px">
      <span class="ico"><svg width="11" height="8" viewBox="0 0 11 8"><rect width="11" height="8" fill="#2b2f3a"/><path d="M0 0l5.5 4.5L11 0" fill="none" stroke="#fff" stroke-width="1"/></svg></span>
      E mail Us<br>info@velora.io
    </div>
  </div>

  <div class="foot-col" style="left:962px">
    <h4>Follow Us</h4>
    <div class="foot-item" style="margin-top:30px"><span class="ico"></span>Like us on<br>CIRCLEBOOK</div>
    <div class="foot-item" style="margin-top:19px"><span class="ico"></span>Follow us on<br>CHIRPER</div>
    <div class="foot-item" style="margin-top:21px"><span class="ico"></span>Follow us on<br>WORKLINK</div>
  </div>

  <div class="foot-rule"></div>
  <div class="copyright">Copyright © 2022 All Rights Reserved</div>
</footer>

</body>
</html>
```